Redesign business cards

We have a new logo and I am not that happy with the layout of our existing card and looking for a change. Font is a bit small and the green can be hard to read. Logo may need a tidy up as the copy I have is not that hi-res too so require you to produce a hi-res version of the logo for us too. There will be three individual business cards to produce with just the names and phone numbers being different. Address will change too, but use what you see on the card for now.

Industry/Entity Type

Business

Requirements
Nice to have
• You could consider a redesign to the new logo, just not too radical. We like the blue and green hexagons as we feel that they are representative of oil industry that we are in.

```html
<!DOCTYPE html>
<html lang="en">
<head>
<meta charset="utf-8">
<title>Corvane Fuel Services – Business Card</title>
<link rel="stylesheet" href="https://fonts.googleapis.com/css2?family=Exo+2:wght@400;500;600&display=swap">
<style>
  :root{
    --page-bg:#e6e4e0;
    --card-orange:#f9ab3f;
    --card-white:#f4f4f4;
    --arc-grey:#6d6e70;
    --ink-white:#ffffff;
    --brand-grey:#6b6c6e;
    --brand-green:#8cc63f;
  }
  *{box-sizing:border-box;margin:0;padding:0}
  html,body{width:1200px;height:900px;overflow:hidden;background:var(--page-bg)}
  body{font-family:"Exo 2",sans-serif;position:relative}
  .business-card{
    position:absolute;left:75px;top:150px;width:1050px;height:600px;
    box-shadow:0 10px 30px rgba(0,0,0,.18);overflow:hidden;background:var(--card-orange);
  }
  .card-shapes{position:absolute;inset:0}
  .contact-block{position:absolute;left:64px;top:58px;color:var(--ink-white)}
  .person-name{font-size:32px;font-weight:500;letter-spacing:2px;text-transform:uppercase}
  .person-role{font-size:20px;font-weight:400;letter-spacing:.5px;margin-top:4px}
  .office-address{font-size:22px;line-height:30px;margin-top:44px;letter-spacing:.5px}
  .contact-list{list-style:none;margin-top:42px}
  .contact-list li{display:flex;align-items:center;gap:14px;font-size:20px;letter-spacing:1px;height:38px}
  .contact-list svg{width:20px;height:20px;flex:none;fill:var(--ink-white)}
  .brand-lockup{position:absolute;left:600px;top:250px;color:var(--brand-grey)}
  .brand-name{display:flex;align-items:center;gap:16px;font-size:76px;font-weight:500;line-height:1}
  .brand-dot{width:40px;height:40px;border-radius:50%;background:var(--brand-green)}
  .brand-tagline{font-size:30px;font-weight:500;margin:6px 0 0 58px}
</style>
</head>
<body>
  <article class="business-card">
    <svg class="card-shapes" viewBox="0 0 1050 600" aria-hidden="true">
      <path fill="var(--card-white)" d="M560 0 C430 90 380 340 450 600 L1050 600 L1050 0 Z"/>
      <path fill="var(--arc-grey)" d="M588 0 C470 80 420 290 446 470 C440 300 486 110 604 0 Z"/>
    </svg>

    <section class="contact-block">
      <h1 class="person-name">Marcus Hale</h1>
      <p class="person-role">Managing Director</p>
      <p class="office-address">210 9th floor, Kestrel<br>Harbour Road QNT</p>
      <ul class="contact-list">
        <li><svg viewBox="0 0 24 24"><path d="M6.6 10.8a15 15 0 0 0 6.6 6.6l2.2-2.2c.3-.3.7-.4 1-.2 1.1.4 2.3.6 3.6.6.6 0 1 .4 1 1V20c0 .6-.4 1-1 1A17 17 0 0 1 3 4c0-.6.4-1 1-1h3.5c.6 0 1 .4 1 1 0 1.3.2 2.5.6 3.6.1.3 0 .7-.2 1z"/></svg>048 217 5530</li>
        <li><svg viewBox="0 0 24 24"><path d="M7 1h10a2 2 0 0 1 2 2v18a2 2 0 0 1-2 2H7a2 2 0 0 1-2-2V3a2 2 0 0 1 2-2zm0 3v14h10V4zm5 15.5a1.2 1.2 0 1 0 0 2.4 1.2 1.2 0 0 0 0-2.4z"/></svg>048 217 5531</li>
        <li><svg viewBox="0 0 24 24"><path d="M6 2h9l3 3v5h2a2 2 0 0 1 2 2v8a2 2 0 0 1-2 2H4a2 2 0 0 1-2-2v-8a2 2 0 0 1 2-2h2zm2 2v6h8V6h-2V4zm-2 10v2h2v-2zm4 0v2h2v-2zm4 0v2h2v-2z"/></svg>048 217 5532</li>
        <li><svg viewBox="0 0 24 24"><path d="M2 5h20v14H2zm2 2v.5l8 5.5 8-5.5V7zm0 2.9V17h16V9.9l-8 5.5z"/></svg>marcus@corvanefuel.com</li>
        <li><svg viewBox="0 0 24 24"><path d="M12 2a10 10 0 1 0 0 20 10 10 0 0 0 0-20zm6.9 9h-3a15 15 0 0 0-1.3-6A8 8 0 0 1 18.9 11zM12 4.1c.9 1.3 1.7 3.8 1.9 6.9h-3.8c.2-3.1 1-5.6 1.9-6.9zM9.4 5A15 15 0 0 0 8.1 11h-3A8 8 0 0 1 9.4 5zM5.1 13h3a15 15 0 0 0 1.3 6A8 8 0 0 1 5.1 13zm6.9 6.9c-.9-1.3-1.7-3.8-1.9-6.9h3.8c-.2 3.1-1 5.6-1.9 6.9zm2.6-.9a15 15 0 0 0 1.3-6h3a8 8 0 0 1-4.3 6z"/></svg>www.corvanefuel.com</li>
      </ul>
    </section>

    <section class="brand-lockup">
      <p class="brand-name"><span class="brand-dot"></span>Corvane</p>
      <p class="brand-tagline">Fuel Services</p>
    </section>
  </article>
</body>
</html>
```